Business Cards for IT Consulting Company (Managed Service Provider)

I am looking to have some business cards printed and would like some designs. We are an IT Consulting company based in Vancouver BC. I would like a nice clean and modern look to the cards. I have uploaded all the versions of my logo so parts can be used as needed. Here is a snippit from our website homepage:

Quillbrook Networks Ltd. is an IT Solutions Partner located in Vancouver BC, Canada. We offer IT solutions and support to customers in the greater Vancouver Area. With expertise in Microsoft platforms, as well as Linux and Mac OSX and over 12 years experience in the IT industry, Quillbrook Networks is dedicated to offering our clients top quality service and products. We take pride in the solutions we offer our customers. The greatest compliment a client can give us is to recommend our services.

Quillbrook Networks Ltd. offers a wide range of IT services from onsite service to remote support and managed service solutions. This allows clients to choose the support path that best suits their company’s needs. Supporting many different sized companies from small to enterprise level over the past 12 years Quillbrook Networks has the experience and expertise needed to ensure things run smoothly. Allowing our clients to focus on doing business.

Revolutionizing the way IT services are delivered.

Quillbrook Networks is dedicated to providing our clients with IT solutions that work and grow with them for years to come. This philosophy helps save money in the long run instead of replacing equipment constantly. Far too often IT solutions are not well thought out and while possibly solving the problem at hand, require replacement due to growth or quality within a very short time frame. Quillbrook Networks takes pride in providing solutions that will last and be able to accommodate growth without the need for replacement.

Industry/Entity Type

Information Technology

Contact Information for Business Card

Quillbrook Networks Ltd.
(Employee Name)
Eml: (Employees Email Address)
Web: quillbrook.me
Ph: 604-555-0148

Font styles to use
Serif
Sans Serif

Requirements
Must have
• The Company logo and company colors.
Nice to have
• - Our tag line: "Dependable IT, Built to Grow" or "Revolutionizing the way IT services are delivered."
• - Also I really like the idea of nature and technology together blending which is sort of where my logo came from so integrating that somehow onto the business cards would be great.

```html
<!DOCTYPE html>
<html lang="en">
<head>
<meta charset="UTF-8">
<title>Quillbrook Networks Ltd. — Business Card</title>
<link rel="stylesheet" href="https://fonts.googleapis.com/css2?family=Source+Sans+3:wght@400;600&display=swap">
<style>
  :root {
    --backdrop: #d6d7d9;
    --card: #f3f4f5;
    --white: #ffffff;
    --brand-blue: #1d95d3;
    --swoosh-gray: #4a4b4d;
    --text-gray: #4d4e50;
    --divider: #c9cacc;
    --pattern-light: #eef2f5;
    --pattern-mid: #dde9f1;
  }
  * { margin: 0; padding: 0; box-sizing: border-box; }
  html, body {
    width: 1105px;
    height: 1200px;
    overflow: hidden;
    background: var(--backdrop);
    font-family: "Source Sans 3", "Myriad Pro", Arial, sans-serif;
  }
  .canvas { position: relative; width: 1105px; height: 1200px; }

  .card {
    position: absolute;
    left: 182px;
    width: 746px;
    height: 427px;
    background: var(--card);
    overflow: hidden;
  }
  .card--front { top: 119px; }
  .card--back { top: 637px; }

  /* Front */
  .wordmark {
    position: absolute;
    left: 66px;
    top: 172px;
    display: flex;
    align-items: center;
    gap: 14px;
    color: var(--brand-blue);
    font-weight: 600;
  }
  .wordmark__square {
    width: 40px;
    height: 40px;
    background: var(--brand-blue);
  }
  .wordmark__name { font-size: 40px; line-height: 1; letter-spacing: -0.5px; }
  .wordmark__suffix { display: block; font-size: 17px; letter-spacing: 1.5px; margin-top: 4px; }

  .divider {
    position: absolute;
    left: 413px;
    top: 105px;
    width: 1px;
    height: 196px;
    background: var(--divider);
  }

  .contact {
    position: absolute;
    left: 446px;
    top: 100px;
    color: var(--text-gray);
  }
  .contact__name {
    color: var(--brand-blue);
    font-size: 29px;
    font-weight: 600;
    line-height: 1;
    margin-bottom: 22px;
  }
  .contact__address { font-size: 19px; line-height: 24px; margin-bottom: 8px; }
  .contact__list { list-style: none; }
  .contact__item {
    display: flex;
    align-items: center;
    gap: 10px;
    font-size: 19px;
    line-height: 28px;
  }
  .contact__icon { width: 16px; height: 16px; flex: none; }

  .swoosh { position: absolute; left: 0; top: 0; width: 746px; height: 427px; }

  /* Back */
  .back-pattern {
    position: absolute;
    inset: 0;
    background: linear-gradient(135deg, var(--pattern-light), var(--pattern-mid) 50%, var(--pattern-light));
  }
  .back-mark {
    position: absolute;
    left: 0;
    right: 0;
    top: 196px;
    text-align: center;
    color: var(--brand-blue);
    font-size: 34px;
    font-weight: 600;
    line-height: 1;
  }
  .tagline {
    position: absolute;
    left: 0;
    right: 0;
    top: 339px;
    text-align: center;
    color: var(--text-gray);
    font-size: 20px;
    font-weight: 600;
    line-height: 24px;
  }
</style>
</head>
<body>
<main class="canvas">

  <section class="card card--front" aria-label="Business card front">
    <div class="wordmark">
      <span class="wordmark__square"></span>
      <span>
        <span class="wordmark__name">Quillbrook</span>
        <span class="wordmark__suffix">NETWORKS LTD.</span>
      </span>
    </div>

    <div class="divider"></div>

    <div class="contact">
      <h1 class="contact__name">Daniel Marsh</h1>
      <p class="contact__address">4120 Cedar Hollow Road<br>Burnaby, BC V5G 2K1</p>
      <ul class="contact__list">
        <li class="contact__item">
          <svg class="contact__icon" viewBox="0 0 16 16" aria-hidden="true">
            <path fill="var(--brand-blue)" d="M3.2 1.2l2.4-.4 1.3 3.2-1.6 1.2c.8 1.9 2.2 3.3 4.1 4.2l1.2-1.6 3.2 1.3-.4 2.4c-.2.9-1 1.5-1.9 1.4C6.2 12.5 2.6 8.9 1.8 3.1c-.1-.9.5-1.7 1.4-1.9z"/>
          </svg>
          <span>604-555-0148</span>
        </li>
        <li class="contact__item">
          <svg class="contact__icon" viewBox="0 0 16 16" aria-hidden="true">
            <rect x="1" y="3" width="14" height="10" fill="var(--brand-blue)"/>
            <path d="M1.5 3.5L8 9l6.5-5.5" fill="none" stroke="var(--card)" stroke-width="1.3"/>
          </svg>
          <span>dmarsh@quillbrook.me</span>
        </li>
        <li class="contact__item">
          <svg class="contact__icon" viewBox="0 0 16 16" aria-hidden="true">
            <circle cx="8" cy="8" r="7" fill="var(--brand-blue)"/>
            <path d="M1 8h14M8 1c-2.5 2.5-2.5 11.5 0 14M8 1c2.5 2.5 2.5 11.5 0 14" fill="none" stroke="var(--card)" stroke-width="1"/>
          </svg>
          <span>www.quillbrook.me</span>
        </li>
      </ul>
    </div>

    <svg class="swoosh" viewBox="0 0 746 427" aria-hidden="true">
      <path d="M0 364 C 200 382, 330 404, 480 402 C 600 400, 700 378, 746 366 L 746 427 L 0 427 Z" fill="var(--white)"/>
      <path d="M0 351 C 200 375, 330 398, 480 396 C 600 394, 700 372, 746 362 L 746 366 C 700 378, 600 400, 480 402 C 330 404, 200 382, 0 364 Z" fill="var(--swoosh-gray)"/>
      <path d="M0 370 C 200 390, 330 410, 480 408 C 600 406, 700 382, 746 371 L 746 427 L 0 427 Z" fill="var(--brand-blue)"/>
    </svg>
  </section>

  <section class="card card--back" aria-label="Business card back">
    <div class="back-pattern" role="img" aria-label="Faint light-blue geometric pattern across the card back"></div>
    <p class="back-mark">Quillbrook Networks Ltd.</p>
    <p class="tagline">Dependable IT, Built to Grow</p>
  </section>

</main>
</body>
</html>
```